Local Roofing/Construction company business needs new biz card design

We need a new business card design, current cards are from the start of this operation and generic at best. We are a local Construction Company (General Contractor) with a majority of our work originating from insurance claims-exterior finish work is the main focus (Roofs-Siding-Gutters etc). Heavily involved with homeowners and the low ball offers they receive from insurance company's after a insurable event takes place. I have attached some of our original logo file(s) below.

```html
<!DOCTYPE html>
<html lang="en">
<head>
<meta charset="utf-8">
<title>Ridgeline Build Co. – Business Card</title>
<link rel="stylesheet" href="https://fonts.googleapis.com/css2?family=Work+Sans:wght@400;600&display=swap">
<style>
  :root {
    --stage: #e9ebe8;
    --green: #45ad64;
    --green-deep: #0f4a35;
    --green-dark: #0c3428;
    --green-glow: #4cbd70;
    --paper: #ffffff;
    --ink: #2e2e2e;
    --muted: #555555;
    --rule: #222222;
  }
  * { box-sizing: border-box; margin: 0; padding: 0; }
  html, body {
    width: 1200px; height: 900px; overflow: hidden;
    background: var(--stage);
    font-family: "Work Sans", Arial, sans-serif;
  }
  .stage {
    position: relative; width: 1200px; height: 900px;
  }
  .card {
    position: absolute; left: 270px; width: 660px; height: 377px;
    border-radius: 28px; overflow: hidden;
    box-shadow: 0 10px 28px rgba(0,0,0,.18);
  }
  /* Back face */
  .card--back { top: 48px; }
  .card-back__field {
    position: absolute; inset: 0;
    background: radial-gradient(ellipse at 42% 45%, var(--green-glow) 0%, #2c8752 38%, var(--green-deep) 75%, var(--green-dark) 100%);
  }
  .card-back__brand {
    position: absolute; right: 40px; bottom: 40px;
    display: flex; align-items: center; gap: 10px;
    color: var(--green-dark); font-weight: 600; font-size: 20px;
    letter-spacing: .04em; text-transform: uppercase;
  }
  .brand-square {
    width: 18px; height: 18px; background: currentColor; flex: none;
  }
  /* Front face */
  .card--front { top: 475px; background: var(--paper); }
  .person { position: absolute; left: 44px; top: 40px; }
  .person__name {
    color: var(--green); font-weight: 600; font-size: 24px;
    letter-spacing: .01em; text-transform: uppercase;
  }
  .person__role { color: var(--muted); font-size: 20px; margin-top: 2px; }
  .brand {
    position: absolute; left: 44px; bottom: 56px; width: 240px;
    display: flex; align-items: center; gap: 10px;
    color: var(--green); font-weight: 600; font-size: 19px;
    letter-spacing: .03em; text-transform: uppercase; line-height: 1.2;
  }
  .brand .brand-square { width: 22px; height: 22px; }
  .divider {
    position: absolute; left: 300px; top: 168px; width: 2px; height: 170px;
    background: var(--rule);
  }
  .contact {
    position: absolute; left: 326px; top: 168px; list-style: none;
    color: var(--ink); font-size: 19px; line-height: 1.25;
  }
  .contact__item { display: flex; align-items: flex-start; gap: 12px; margin-bottom: 10px; }
  .contact__icon { width: 20px; height: 20px; flex: none; margin-top: 2px; }
</style>
</head>
<body>
<main class="stage">
  <section class="card card--back">
    <div class="card-back__field" role="img" aria-label="Repeating brand pattern on a green gradient"></div>
    <div class="card-back__brand"><span class="brand-square"></span>Ridgeline Build Co.</div>
  </section>

  <section class="card card--front">
    <div class="person">
      <p class="person__name">Dana Whitfield</p>
      <p class="person__role">Director</p>
    </div>

    <div class="brand"><span class="brand-square"></span>Ridgeline Build Co.</div>

    <div class="divider"></div>

    <ul class="contact">
      <li class="contact__item">
        <svg class="contact__icon" viewBox="0 0 24 24" fill="var(--green)"><path d="M6.6 10.8a15.1 15.1 0 0 0 6.6 6.6l2.2-2.2a1 1 0 0 1 1-.25 11.4 11.4 0 0 0 3.6.57 1 1 0 0 1 1 1V20a1 1 0 0 1-1 1A17 17 0 0 1 3 4a1 1 0 0 1 1-1h3.5a1 1 0 0 1 1 1c0 1.25.2 2.45.57 3.57a1 1 0 0 1-.25 1z"/></svg>
        <span>555-210-4830</span>
      </li>
      <li class="contact__item">
        <svg class="contact__icon" viewBox="0 0 24 24" fill="var(--green)"><path d="M2 5h20v14H2z"/><path d="M2 5l10 8 10-8" fill="none" stroke="#fff" stroke-width="2"/></svg>
        <span>hello@ridgelinebuild.com</span>
      </li>
      <li class="contact__item">
        <svg class="contact__icon" viewBox="0 0 24 24" fill="none" stroke="var(--green)" stroke-width="2"><circle cx="12" cy="12" r="9"/><path d="M3 12h18M12 3c3 3 3 15 0 18M12 3c-3 3-3 15 0 18"/></svg>
        <span>www.ridgelinebuild.com</span>
      </li>
      <li class="contact__item">
        <svg class="contact__icon" viewBox="0 0 24 24" fill="var(--green)"><path d="M12 2a7 7 0 0 0-7 7c0 5 7 13 7 13s7-8 7-13a7 7 0 0 0-7-7zm0 9.5A2.5 2.5 0 1 1 12 6.5a2.5 2.5 0 0 1 0 5z"/></svg>
        <span>48 Maple Hollow<br>Dr, Fairview, MO 63012</span>
      </li>
    </ul>
  </section>
</main>
</body>
</html>
```